Professional, modern and unique business card. We are looking to present a new look to our business cards however we don't want to divert too far away from original template. We want social media links and our 3 office addresses on the backside of the business cards. Please see attached business card templates for ideas.
Crestline Homes Color Code:
R: 7
G:63
B:86

Target Market(s)

Real Estate

Industry/Entity Type

Real Estate

Contact Information for Business Card

Follow the attached templates. In need of a more modern and unique touch but don't want to divert from the original theme or color.
Crestline Homes Color Code:
R: 7
G:63
B:86

Font styles to use
Serif

Requirements
Must have
• Crestline Homes logo, Crestline homes colors, social media links, 3 office addresses,
Nice to have
• information about Crestline Homes and QR codes. You can check out www.mycrestlinehomes.example

```html
<!DOCTYPE html>
<html lang="en">
<head>
<meta charset="utf-8">
<title>Crestline Homes – Business Card</title>
<link href="https://fonts.googleapis.com/css2?family=Lato:wght@400;700&display=swap" rel="stylesheet">
<style>
  :root {
    --stage: #3a3b3e;
    --card-blue: #1676b2;
    --card-blue-deep: #0f67a0;
    --ink-light: #f2f8fc;
    --logo-tint: #d6e9f4;
    --strip-top: #f4fbff;
    --strip-bottom: #9fd2ea;
    --rule: rgba(255,255,255,0.28);
  }
  * { box-sizing: border-box; margin: 0; padding: 0; }
  html, body { width: 1200px; height: 896px; overflow: hidden; }
  body {
    background: var(--stage);
    font-family: "Lato", sans-serif;
    color: var(--ink-light);
    display: flex; flex-direction: column; align-items: center; justify-content: center;
    gap: 36px;
  }
  .card {
    position: relative;
    width: 700px; height: 400px;
    background: linear-gradient(160deg, var(--card-blue) 0%, var(--card-blue-deep) 100%);
    box-shadow: 0 10px 30px rgba(0,0,0,0.45);
    overflow: hidden;
  }
  .card::after {
    content: ""; position: absolute; left: 0; right: 0; bottom: 0; height: 14px;
    background: linear-gradient(180deg, var(--strip-top), var(--strip-bottom));
  }
  .icon { width: 16px; height: 16px; flex: none; fill: var(--ink-light); }

  /* front */
  .contact { position: absolute; left: 56px; top: 110px; }
  .contact .name { font-weight: 700; font-size: 25px; letter-spacing: 1px; text-transform: uppercase; }
  .contact .role { font-size: 17px; margin: 2px 0 12px; }
  .contact .line { display: flex; align-items: center; gap: 8px; font-size: 17px; line-height: 23px; }
  .brand {
    position: absolute; left: 370px; top: 140px;
    display: flex; align-items: center; gap: 12px;
    color: var(--logo-tint);
  }
  .brand .mark { width: 22px; height: 22px; border-radius: 50%; border: 2px solid var(--logo-tint); }
  .brand .wordmark { font-weight: 700; font-size: 34px; letter-spacing: 1px; }
  .front .rule { position: absolute; left: 330px; right: 48px; top: 272px; height: 1px; background: var(--rule); }
  .web { position: absolute; right: 48px; top: 290px; text-align: right; }
  .web .line { display: flex; align-items: center; justify-content: flex-end; gap: 8px; font-size: 17px; line-height: 24px; }

  /* back */
  .socials {
    position: absolute; left: 48px; top: 70px; right: 40px;
    display: grid; grid-template-columns: 1fr 1.3fr 1.1fr; row-gap: 14px; column-gap: 14px;
  }
  .social { display: flex; align-items: center; gap: 8px; font-size: 16px; white-space: nowrap; }
  .social .dot { width: 20px; height: 20px; border-radius: 50%; background: var(--ink-light); flex: none; }
  .offices {
    position: absolute; left: 48px; right: 40px; top: 190px;
    display: grid; grid-template-columns: 1fr 1fr 1fr; column-gap: 14px;
  }
  .office { font-size: 17px; line-height: 23px; white-space: nowrap; }
  .office:nth-child(2) { margin-top: 38px; }
  .office:nth-child(3) { margin-top: 76px; }
</style>
</head>
<body>

<section class="card front" aria-label="Card front">
  <div class="contact">
    <p class="name">Daniel Harper</p>
    <p class="role">Managing Director</p>
    <p class="line"><svg class="icon" viewBox="0 0 16 16"><path d="M3 2h3l1 3-2 1a8 8 0 0 0 5 5l1-2 3 1v3a1 1 0 0 1-1 1A12 12 0 0 1 2 3a1 1 0 0 1 1-1z"/></svg>044-555 010 200</p>
    <p class="line"><svg class="icon" viewBox="0 0 16 16"><path d="M5 1h6a1 1 0 0 1 1 1v12a1 1 0 0 1-1 1H5a1 1 0 0 1-1-1V2a1 1 0 0 1 1-1zm0 2v9h6V3zm3 10a.8.8 0 1 0 0 1.6.8.8 0 0 0 0-1.6z"/></svg>044-555 010 201</p>
    <p class="line"><svg class="icon" viewBox="0 0 16 16"><path d="M4 1h7v4H4zM2 6h12a1 1 0 0 1 1 1v5h-2v3H3v-3H1V7a1 1 0 0 1 1-1zm3 5v2h6v-2z"/></svg>044-555 010 202</p>
  </div>

  <div class="brand">
    <span class="mark"></span>
    <span class="wordmark">Crestline Homes</span>
  </div>

  <div class="rule"></div>
  <div class="web">
    <p class="line">info@crestlinehomes.example<svg class="icon" viewBox="0 0 16 16"><path d="M1 3h14v10H1zm1.5 1.2L8 8.5l5.5-4.3z"/></svg></p>
    <p class="line">www.mycrestlinehomes.example<svg class="icon" viewBox="0 0 16 16"><circle cx="8" cy="8" r="7"/></svg></p>
  </div>
</section>

<section class="card back" aria-label="Card back">
  <div class="socials">
    <p class="social"><span class="dot"></span>CrestlinehomesNY</p>
    <p class="social"><span class="dot"></span>Info at Crestline Homes</p>
    <p class="social"><span class="dot"></span>@CrestlineHomesNY</p>
    <p class="social"><span class="dot"></span>Crestline Homes</p>
    <p class="social"><span class="dot"></span>Crestline Homes New York</p>
    <p class="social"><span class="dot"></span>@CrestlineHomesQ</p>
  </div>
  <div class="offices">
    <p class="office">312-08 Harbor Ln<br>Harbor Point, NY 10990</p>
    <p class="office">77-40 Cedar Row<br>Maple Grove, NY 10991</p>
    <p class="office">940 Linden Ave<br>Eastbrook, NY 10992</p>
  </div>
</section>

</body>
</html>
```